Business Card Design

We are a commercial real estate brokerage in San Francisco, leasing office buildings downtown.
I would like a clean, elegant look. Simple but powerful .

Industry/Entity Type

Business

Contact Information for Business Card

Derek Holloway
lic# 07258143
415.555.0172
derek@velt-commercial.example
velt-commercial.example

```html
<!DOCTYPE html>
<html lang="en">
<head>
<meta charset="utf-8">
<title>Velt Commercial – Business Card</title>
<link rel="stylesheet" href="https://fonts.googleapis.com/css2?family=Arimo:wght@400;700&display=swap">
<style>
  :root {
    --page-bg: #e6e7ea;
    --card-white: #ffffff;
    --slate-blue: #7a8eac;
    --slate-blue-dark: #5f7291;
    --divider-shadow: #4b5566;
    --ink-grey: #555a61;
    --brand-blue: #7385a6;
    --on-panel: #ffffff;
    --skyline-dark: #3f4247;
    --skyline-light: #b9bcc2;
  }
  * { box-sizing: border-box; margin: 0; padding: 0; }
  html, body {
    width: 1200px; height: 950px; overflow: hidden;
    background: var(--page-bg);
    font-family: "Arimo", Arial, sans-serif;
  }
  .canvas { position: relative; width: 1200px; height: 950px; }
  .card {
    position: absolute; left: 230px; width: 740px; height: 423px;
    background: var(--card-white);
    box-shadow: 0 6px 18px rgba(0,0,0,0.18);
    overflow: hidden;
  }
  .card--back { top: 40px; }
  .card--front { top: 487px; display: flex; }

  /* back side */
  .skyline-art {
    position: absolute; left: 220px; top: 88px; width: 300px; height: 120px;
    background: linear-gradient(90deg, var(--skyline-light), var(--skyline-dark) 45%, var(--skyline-light));
    opacity: 0.85;
  }
  .tagline {
    position: absolute; left: 0; right: 0; top: 262px;
    text-align: center; color: var(--ink-grey);
    font-size: 17px; line-height: 1.3; letter-spacing: 0.2px;
  }

  /* front side */
  .contact-panel {
    position: relative; flex: none; width: 380px; height: 100%;
    background: linear-gradient(160deg, var(--slate-blue), var(--slate-blue-dark));
    color: var(--on-panel);
    padding: 150px 0 0 44px;
    border-right: 3px solid var(--divider-shadow);
    box-shadow: 3px 0 6px rgba(0,0,0,0.25);
  }
  .contact-name { font-size: 26px; font-weight: 700; margin-bottom: 12px; white-space: nowrap; }
  .contact-list { list-style: none; font-size: 17px; line-height: 1.55; }
  .contact-list li { display: flex; align-items: center; gap: 10px; white-space: nowrap; }
  .contact-list .icon { width: 15px; height: 15px; flex: none; }

  .brand-side {
    flex: 1; display: flex; align-items: center; justify-content: center;
  }
  .brand-lockup { display: flex; align-items: center; gap: 12px; }
  .brand-square { width: 16px; height: 16px; background: var(--brand-blue); flex: none; }
  .brand-name {
    font-size: 28px; font-weight: 400; color: var(--brand-blue);
    white-space: nowrap;
  }
</style>
</head>
<body>
<main class="canvas">

  <section class="card card--back" aria-label="Card back">
    <div class="skyline-art" role="img" aria-label="Illustration of downtown office towers"></div>
    <p class="tagline">commercial real estate brokerage in San Francisco<br>leasing office buildings downtown.</p>
  </section>

  <section class="card card--front" aria-label="Card front">
    <div class="contact-panel">
      <h1 class="contact-name">Derek Holloway</h1>
      <ul class="contact-list">
        <li>lic# 07258143</li>
        <li>
          <svg class="icon" viewBox="0 0 16 16" aria-hidden="true"><path fill="currentColor" d="M2 6c0-2 2-3 6-3s6 1 6 3l-2 1-1-2H5L4 7 2 6zm2 2h8l1 5H3l1-5zm4 1.5a1.5 1.5 0 1 0 0 3 1.5 1.5 0 0 0 0-3z"/></svg>
          415.555.0172
        </li>
        <li>
          <svg class="icon" viewBox="0 0 16 16" aria-hidden="true"><rect x="1" y="3.5" width="14" height="9" fill="currentColor"/><path d="M1.5 4l6.5 5 6.5-5" fill="none" stroke="#7a8eac" stroke-width="1.3"/></svg>
          derek@velt-commercial.example
        </li>
        <li>
          <svg class="icon" viewBox="0 0 16 16" aria-hidden="true"><circle cx="8" cy="8" r="7" fill="currentColor"/><path d="M4 7h8M4 10h8M8 1.5c-2.5 3-2.5 10 0 13" fill="none" stroke="#7a8eac" stroke-width="1"/></svg>
          velt-commercial.example
        </li>
      </ul>
    </div>
    <div class="brand-side">
      <div class="brand-lockup">
        <span class="brand-square" aria-hidden="true"></span>
        <span class="brand-name">Velt Commercial</span>
      </div>
    </div>
  </section>

</main>
</body>
</html>
```